Postcard Design

Law office.
Details are on the attached pdf file:
NOTE: the following items are to be changed, as follows:
1. price is 799
2. delete "Expires 2-8-13"
3. make "Nevada County's..." into "Northern California's ... "
4. Someplace where it fits nicely, add "Fast, Easy, Done!"
5. Delete "no obligation first visit"
6. That attached pdf was a successful ad so I want to maintain that look GENERALLY, but I'm not stuck on anything in particular. Some freedom to play with it for a perfect ad.
7. I'll attach the revised picture and the logo.

Office

```html
<!DOCTYPE html>
<html lang="en">
<head>
<meta charset="utf-8">
<title>Estate Plans Postcard</title>
<link rel="stylesheet" href="https://fonts.googleapis.com/css2?family=EB+Garamond:ital,wght@0,400;0,500;0,600;0,700;1,400;1,600&display=swap">
<style>
  :root {
    --ink: #231f20;
    --bg-edge: #c9c9c9;
    --bg-mid: #e4e4e4;
    --photo-dark: #3a3a3c;
    --photo-light: #b9b4b0;
  }
  html, body {
    margin: 0;
    padding: 0;
    overflow: hidden;
    background: #ffffff;
  }
  .postcard {
    position: relative;
    width: 1200px;
    height: 862px;
    overflow: hidden;
    background: radial-gradient(ellipse at 55% 45%, var(--bg-mid) 0%, #d8d8d8 55%, var(--bg-edge) 100%);
    font-family: "EB Garamond", Georgia, serif;
    color: var(--ink);
  }
  .postcard > * { position: absolute; margin: 0; }
  .headline {
    left: 0; width: 1200px; top: 48px;
    text-align: center;
    font-size: 54px; font-weight: 600;
    letter-spacing: -1.2px;
    line-height: 1;
  }
  .subline {
    left: 0; width: 1200px; top: 130px;
    text-align: center;
    font-size: 44px; font-style: italic; font-weight: 400;
    letter-spacing: 0.5px;
    line-height: 1;
  }
  .price {
    left: 202px; top: 200px;
    font-size: 150px; font-weight: 600;
    letter-spacing: -2px;
    line-height: 1;
  }
  .value-note {
    left: 676px; top: 258px;
    font-size: 25px; font-weight: 600;
    letter-spacing: 1px;
    line-height: 1;
  }
  .tagline {
    left: 674px; top: 296px;
    font-size: 34px; font-weight: 600;
    line-height: 1;
  }
  .protect {
    left: 0; width: 1200px; top: 402px;
    text-align: center;
    font-size: 56px; font-weight: 600;
    line-height: 1;
  }
  .call-now {
    left: 200px; width: 800px; top: 470px;
    text-align: center;
    font-size: 33px; font-weight: 600;
    line-height: 1;
  }
  .portrait {
    left: 0; top: 468px;
    width: 352px; height: 394px;
  }
  .office-label {
    left: 460px; top: 556px;
    font-size: 33px; font-weight: 400;
    line-height: 1;
  }
  .attorney-name {
    left: 312px; width: 700px; top: 598px;
    text-align: center;
    font-size: 80px; font-weight: 400;
    line-height: 1;
  }
  .phone {
    left: 312px; width: 700px; top: 732px;
    text-align: center;
    font-size: 36px; font-weight: 600;
    letter-spacing: 1px;
    line-height: 1;
  }
  .website {
    left: 312px; width: 700px; top: 772px;
    text-align: center;
    font-size: 26px; font-style: italic; font-weight: 600;
    line-height: 1;
  }
  .notary {
    left: 312px; width: 700px; top: 806px;
    text-align: center;
    font-size: 23px; font-weight: 400;
    line-height: 1;
  }
  .brand-mark {
    left: 1040px; top: 598px;
    width: 140px; height: 166px;
    text-align: center;
  }
  .brand-square {
    display: block;
    margin: 0 auto 10px;
    width: 96px; height: 96px;
    border: 3px solid var(--ink);
    box-sizing: border-box;
  }
  .brand-name {
    font-size: 26px; font-weight: 600;
    line-height: 1.05;
    color: var(--ink);
  }
  .since {
    left: 1030px; width: 160px; top: 790px;
    text-align: center;
    font-size: 18px; font-style: italic;
    line-height: 1.2;
  }
</style>
</head>
<body>
  <div class="postcard">
    <h1 class="headline">Northern California's Best in Estate Plans</h1>
    <p class="subline">Living Trusts, Wills &amp; All Necessary Documents</p>

    <p class="price">$799</p>
    <p class="value-note">OVER $2,000 VALUE</p>
    <p class="tagline">Fast, Easy, Done!</p>

    <p class="protect">Protect Your Loved Ones!</p>
    <p class="call-now">It’s Easy — Call Now!</p>

    <svg class="portrait" role="img" aria-label="Portrait photo of the attorney in a dark suit and tie" viewBox="0 0 352 394" xmlns="http://www.w3.org/2000/svg">
      <defs>
        <linearGradient id="portraitTone" x1="0" y1="0" x2="0" y2="1">
          <stop offset="0" stop-color="var(--photo-light)"/>
          <stop offset="0.55" stop-color="#6e6a68"/>
          <stop offset="1" stop-color="var(--photo-dark)"/>
        </linearGradient>
      </defs>
      <rect x="0" y="0" width="352" height="394" fill="url(#portraitTone)"/>
    </svg>

    <p class="office-label">Law Office Of</p>
    <p class="attorney-name">Daniel R. Moretti</p>

    <p class="phone">555-0142</p>
    <p class="website">Check me out at: www.DanielMoretti.com</p>
    <p class="notary">Free Notarization</p>

    <div class="brand-mark">
      <span class="brand-square"></span>
      <span class="brand-name">Moretti Law</span>
    </div>
    <p class="since">Thousands Served<br>Since 1998</p>
  </div>
</body>
</html>
```